VELQUINT

1. My company will allow people to buy either stock made or custom scented aromatherapy candles, lotions,soaps,body sprays, and wax melts. As there isn't a company that allows for custom oil scent mixes but me. We are just starting with the candles and the other items will be coming later.

2. My target audience is anyone who would want to buy my product. It isn't really limited due to the nature of the product I will be providing.

3. velquint.com is the domain name (purchased from plorvex.com).

4. So what I really need is the shopping cart function. A fully coded shopping cart that will calculate shipping and sales tax if need be. I need the cart function to be just like every other major retailers shopping cart function. So they can click on an item they want and have it go into a shopping cart for the customer to then be able to go and pay for their goods. I also need help creating single pages for each product. So that each thing we make has a separate page with a description and an add to cart button.

5. I would like the color scheme to follow the logo I made. I would also like the logo top center of first page. I would like the quote " elevate your choices in aromatherapy products"

^. I basically need a checkout just like every other good website. A clear shipping area for them to populate, sales tax calculator, ya know everything a normal checkout has like tressly or dunvexa.com. I also have a vonk account already as well.

```html
<!DOCTYPE html>
<html lang="en">
<head>
<meta charset="utf-8">
<title>VELQUINT — Aromatherapy Candles</title>
<link href="https://fonts.googleapis.com/css2?family=Montserrat:wght@400;500;600;700;800&family=Poppins:wght@400;500;600;700&display=swap" rel="stylesheet">
<style>
:root{
  --purple:#6a3cc4;
  --purple-deep:#5a2fb0;
  --purple-mid:#7c47d2;
  --purple-light:#9a5bdc;
  --accent:#8e4fd0;
  --ink:#1d1d1f;
  --text:#3a3a3a;
  --muted:#6b6b6b;
  --tile:#f4f4f4;
  --white:#ffffff;
}
*{box-sizing:border-box;margin:0;padding:0}
html,body{width:1200px;height:3863px;overflow:hidden}
body{position:relative;background:var(--white);font-family:'Poppins',sans-serif;color:var(--text)}
.abs{position:absolute}

/* Hero */
.hero-photo{left:0;top:0;width:1200px;height:890px;
  background:
    radial-gradient(ellipse 170px 240px at 790px 420px,#b25ad6 0%,#8f3fc0 45%,rgba(120,60,170,0) 100%),
    radial-gradient(ellipse 300px 360px at 1020px 380px,rgba(190,140,225,.85) 0%,rgba(150,100,200,0) 100%),
    radial-gradient(ellipse 320px 220px at 250px 180px,rgba(200,170,225,.7) 0%,rgba(160,130,190,0) 100%),
    linear-gradient(180deg,#9d7fc0 0%,#7f63a4 45%,#5e5077 75%,#4a4358 100%)}
.nav{left:138px;top:105px;width:924px;height:68px;background:var(--purple);opacity:.95}
.nav a{position:absolute;top:0;height:68px;line-height:68px;color:var(--white);font-family:'Montserrat',sans-serif;font-weight:700;font-size:14px;text-decoration:none}
.nav .active{background:var(--purple-light);padding:0 16px}
.cart-badge{position:absolute;top:14px;left:875px;width:16px;height:16px;border-radius:50%;background:var(--purple-light);color:#fff;font-size:10px;line-height:16px;text-align:center;font-family:'Montserrat',sans-serif}
.brand-badge{left:495px;top:33px;width:210px;height:210px;border-radius:50%;background:var(--white);border:6px solid var(--purple);display:flex;align-items:center;justify-content:center}
.brand-badge span{font-family:'Montserrat',sans-serif;font-weight:800;font-size:30px;color:var(--purple);letter-spacing:1px}
.hero-title{left:168px;top:268px;width:470px;font-family:'Montserrat',sans-serif;font-weight:400;font-size:44px;line-height:48px;color:var(--white)}
.btn{display:inline-block;border-radius:30px;font-family:'Montserrat',sans-serif;font-weight:700;text-align:center}
.btn-hero{left:163px;top:450px;width:176px;height:50px;line-height:50px;background:var(--purple);color:#fff;font-size:18px}
.dots{left:172px;top:534px;display:flex;gap:15px}
.dots i{width:11px;height:11px;border-radius:50%;background:#2fb6e6;display:block}
.dots i:first-child{background:#fff}
.wave{left:0;top:560px}

/* Products */
.section-title{left:0;width:1200px;text-align:center;font-family:'Montserrat',sans-serif;font-weight:700;color:var(--ink)}
.headline{top:812px;font-size:40px;line-height:49px}
.headline em{font-style:normal;color:var(--accent)}
.tabs{left:366px;top:937px;display:flex;align-items:center;gap:19px;font-size:15px;color:var(--purple)}
.tabs .on{background:var(--purple);color:#fff;border-radius:20px;width:124px;height:36px;line-height:36px;text-align:center}
.product{width:224px}
.product .shot{width:224px;height:288px;position:relative;background-color:var(--tile)}
.product.white .shot{background-color:#fff;border:1px solid #f0f0f0}
.product .name{margin-top:12px;padding-left:6px;font-size:15px;color:var(--text)}
.product .price{padding-left:6px;font-size:15px;margin-top:2px}
.product .price s{color:var(--muted)}
.product .price b{color:var(--ink);font-weight:600;margin-left:4px}
.tone-peach{background-image:radial-gradient(ellipse 80px 70px at 50% 42%,#d98a6e 0%,#c47a66 40%,#a9a68e 70%,rgba(244,244,244,0) 100%)}
.tone-charcoal{background-image:radial-gradient(ellipse 80px 70px at 50% 42%,#2a2a2a 0%,#3a3a3a 50%,rgba(255,255,255,0) 100%)}
.tone-rose{background-image:radial-gradient(ellipse 52px 80px at 48% 42%,#e0aa92 0%,#d9a088 45%,rgba(244,244,244,0) 100%)}
.tone-magenta{background-image:radial-gradient(ellipse 55px 60px at 50% 48%,#d04c86 0%,#7e2d6a 50%,rgba(255,255,255,0) 100%)}
.tone-holly{background-image:radial-gradient(ellipse 58px 68px at 50% 48%,#efe8d8 0%,#b7c0a0 45%,#5f7a52 65%,rgba(244,244,244,0) 100%)}
.tone-blue{background-image:radial-gradient(ellipse 95px 50px at 50% 52%,#3e5fa8 0%,#8d8ab0 45%,#d9bc98 65%,rgba(255,255,255,0) 100%)}
.tone-amber{background-image:radial-gradient(ellipse 70px 62px at 50% 45%,#4a2414 0%,#6b3a1c 40%,#c9a47c 65%,rgba(244,244,244,0) 100%)}
.tone-lavender{background-image:radial-gradient(ellipse 95px 50px at 50% 48%,#a98bd8 0%,#b9a5d6 45%,#d8d0e0 65%,rgba(255,255,255,0) 100%)}
.product-tools{position:absolute;left:20px;bottom:24px;display:flex;gap:15px}
.product-tools span{width:36px;height:36px;background:#fff;border:1px solid #ddd;display:flex;align-items:center;justify-content:center}

/* Custom */
.custom{left:0;top:1960px;width:1200px;height:476px}
.custom-photo{position:absolute;inset:0;background:
  radial-gradient(ellipse 160px 110px at 90px 60px,rgba(60,100,200,.8) 0%,rgba(60,100,200,0) 100%),
  radial-gradient(ellipse 170px 150px at 380px 170px,#f3e6cc 0%,#d9a25a 45%,rgba(160,100,50,0) 100%),
  linear-gradient(160deg,#8a5a36 0%,#a87048 30%,#c9a070 55%,#7a5434 100%)}
.custom-panel{position:absolute;inset:0;background:linear-gradient(135deg,var(--purple-mid),var(--purple-deep));clip-path:polygon(660px 0,1200px 0,1200px 476px,578px 476px)}
.custom h2{position:absolute;left:713px;top:65px;font-family:'Montserrat',sans-serif;font-weight:800;font-size:40px;line-height:46px;color:#fff}
.custom p.lead{position:absolute;left:713px;top:216px;width:300px;font-size:11px;line-height:14px;color:#fff}
.btn-light{background:#fff;color:var(--purple);font-size:18px;height:42px;line-height:42px}
.testimonial{position:absolute;left:138px;top:308px;width:365px;height:120px;border-radius:60px;background:rgba(142,79,208,.94);color:#fff}
.avatar{position:absolute;left:28px;top:14px;width:92px;height:92px;border-radius:50%;background:linear-gradient(#efe9f5,#d8c6ec);border:3px solid #fff}
.testimonial p.quote{position:absolute;left:120px;top:22px;width:200px;font-size:11px;line-height:14px}
.testimonial b{position:absolute;left:120px;top:88px;font-size:11px}

/* Blogs */
.blogs-title{top:2508px;font-size:40px}
.blog{width:286px}
.blog .shot{height:201px;border-radius:6px}
.blog h3{margin:24px 4px 0;max-width:240px;font-family:'Montserrat',sans-serif;font-weight:700;font-size:22px;line-height:27px;color:#2b2b2b}
.blog time{display:block;margin:4px 4px 0;font-size:13px;color:var(--text)}
.blog p{margin:12px 4px 0;font-size:13px;line-height:19px;color:var(--text)}

/* About */
.about{left:0;top:3072px;width:1200px;height:471px}
.about-photo{position:absolute;inset:0;background:
  radial-gradient(ellipse 110px 130px at 975px 230px,#f0dcc0 0%,#d6a878 40%,rgba(120,80,50,0) 100%),
  radial-gradient(ellipse 90px 60px at 1045px 420px,rgba(240,190,130,.8) 0%,rgba(120,80,50,0) 100%),
  radial-gradient(ellipse 500px 300px at 900px 260px,#6a4a36 0%,#3a2a20 60%,#1e1612 100%)}
.about-panel{position:absolute;inset:0;background:linear-gradient(135deg,var(--purple-mid),var(--purple));clip-path:polygon(0 0,678px 0,615px 471px,0 471px)}
.about h2{position:absolute;left:144px;top:64px;font-family:'Montserrat',sans-serif;font-weight:800;font-size:40px;color:#fff}
.about p{position:absolute;left:144px;width:410px;font-size:13px;line-height:19px;color:#fff}

/* Footer */
.footer-badge{left:146px;top:3589px;width:156px;height:156px;border-radius:50%;border:5px solid var(--purple);display:flex;align-items:center;justify-content:center;font-family:'Montserrat',sans-serif;font-weight:800;font-size:22px;color:var(--purple)}
.fcol{top:3604px}
.fcol h4{font-family:'Montserrat',sans-serif;font-weight:700;font-size:20px;color:var(--accent);margin-bottom:6px}
.fcol li{list-style:none;font-size:13px;line-height:24px;color:var(--text)}
.socials{left:139px;top:3778px;display:flex;gap:13px}
.socials span{width:37px;height:37px;border-radius:50%;border:1px solid var(--purple);font-size:9px;font-weight:600;color:var(--purple);display:flex;align-items:center;justify-content:center}
.socials span:first-child{background:var(--purple);color:#fff}
.pay{left:470px;top:3784px;display:flex;gap:10px}
.pay span{font-size:11px;font-weight:600;color:var(--purple);padding:3px 6px;border:1px solid #ddd;border-radius:3px}
.copyright{left:870px;top:3788px;font-size:13px;color:var(--text)}
</style>
</head>
<body>

<!-- Hero -->
<div class="abs hero-photo" role="img" aria-label="Photo of a lit purple pillar candle surrounded by lavender blossoms"></div>
<nav class="abs nav">
  <a class="active" style="left:68px">Home</a>
  <a style="left:156px">About Us</a>
  <a style="left:251px">Products</a>
  <a style="left:594px">Customize</a>
  <a style="left:697px">Blog</a>
  <a style="left:760px">Contact Us</a>
  <svg style="position:absolute;left:862px;top:24px" width="22" height="20" viewBox="0 0 22 20" fill="none" stroke="#fff" stroke-width="2"><path d="M1 2h4l3 11h10l3-8H7"/><circle cx="9" cy="17" r="1.5" fill="#fff"/><circle cx="17" cy="17" r="1.5" fill="#fff"/></svg>
  <span class="cart-badge">0</span>
</nav>
<div class="abs brand-badge"><span>VELQUINT</span></div>
<h1 class="abs hero-title">Elevate your choices in aromatherapy products</h1>
<a class="abs btn btn-hero">Shop Now</a>
<div class="abs dots"><i></i><i></i><i></i><i></i></div>
<svg class="abs wave" width="1200" height="332" viewBox="0 0 1200 332">
  <path d="M0 205 C120 80 220 40 330 40 C480 40 560 180 750 175 C950 170 1100 190 1200 160 L1200 332 L0 332Z" fill="#6a3cc4"/>
  <path d="M0 320 C120 150 230 80 340 80 C500 80 580 220 770 222 C960 224 1110 250 1200 322 L1200 332 L0 332Z" fill="#ffffff"/>
</svg>

<!-- Products -->
<h2 class="abs section-title headline">Candles which will<br>take away <em>all your worries</em></h2>
<div class="abs tabs"><span class="on">All Candle</span><span>Lotions</span><span>Soaps</span><span>Body</span><span>Sprays</span><span>Wax melts</span></div>

<div class="abs product" style="left:123px;top:1032px">
  <div class="shot tone-peach" role="img" aria-label="Stack of peach, coral and sage pillar candles tied with twine">
    <div class="product-tools">
      <span><svg width="14" height="14" viewBox="0 0 14 14" fill="none" stroke="#333" stroke-width="1.4"><circle cx="6" cy="6" r="4.5"/><path d="M9.5 9.5L13 13M4 6h4M6 4v4"/></svg></span>
      <span><svg width="14" height="14" viewBox="0 0 14 14" fill="none" stroke="#333" stroke-width="1.4"><path d="M1 2h2l2 7h6l2-5H4"/><circle cx="6" cy="12" r="1"/><circle cx="11" cy="12" r="1"/></svg></span>
      <span><svg width="14" height="14" viewBox="0 0 14 14" fill="none" stroke="#333" stroke-width="1.4"><path d="M7 12S1.5 8.5 1.5 5A2.8 2.8 0 0 1 7 3.5 2.8 2.8 0 0 1 12.5 5C12.5 8.5 7 12 7 12Z"/></svg></span>
      <span><svg width="14" height="14" viewBox="0 0 14 14" fill="none" stroke="#333" stroke-width="1.4"><path d="M2 5h10M9 2l3 3M12 9H2M5 12L2 9"/></svg></span>
    </div>
  </div>
  <div class="name">Eucalyptus Essential Oil</div><div class="price"><s>$10.00</s><b>$5.00</b></div>
</div>
<div class="abs product white" style="left:366px;top:1071px">
  <div class="shot tone-charcoal" role="img" aria-label="Black ceramic bowl candles with dark stones"></div>
  <div class="name">3 Wick Candles</div><div class="price"><s>$10.00</s><b>$5.00</b></div>
</div>
<div class="abs product" style="left:610px;top:1032px">
  <div class="shot tone-rose" role="img" aria-label="Rose gold jar candle with blank label"></div>
  <div class="name">Citrus Burst</div><div class="price"><s>$10.00</s><b>$5.00</b></div>
</div>
<div class="abs product white" style="left:853px;top:1071px">
  <div class="shot tone-magenta" role="img" aria-label="Pink and purple glass bell jar candle"></div>
  <div class="name">lemongrass bell jar candle</div><div class="price"><s>$10.00</s><b>$5.00</b></div>
</div>
<div class="abs product" style="left:123px;top:1416px">
  <div class="shot tone-holly" role="img" aria-label="Cream pillar candle decorated with holly leaves"></div>
  <div class="name">Eucalyptus Essential Oil</div><div class="price"><s>$10.00</s><b>$5.00</b></div>
</div>
<div class="abs product white" style="left:366px;top:1455px">
  <div class="shot tone-blue" role="img" aria-label="Blue speckled and beige ceramic bowl candles"></div>
  <div class="name">3 Wick Candles</div><div class="price"><s>$10.00</s><b>$5.00</b></div>
</div>
<div class="abs product" style="left:610px;top:1416px">
  <div class="shot tone-amber" role="img" aria-label="Amber glass jar candle with wooden lid"></div>
  <div class="name">Woodland Escape</div><div class="price"><s>$10.00</s><b>$5.00</b></div>
</div>
<div class="abs product white" style="left:853px;top:1455px">
  <div class="shot tone-lavender" role="img" aria-label="Lavender glass candles with dried lavender sprigs"></div>
  <div class="name">Lavender Dreams</div><div class="price"><s>$10.00</s><b>$5.00</b></div>
</div>

<!-- Customized candles -->
<section class="abs custom">
  <div class="custom-photo" role="img" aria-label="Amber jar candle on a wicker tray with blue flowers"></div>
  <div class="custom-panel"></div>
  <h2>We Sell<br>Customized<br>Candles</h2>
  <p class="lead">Lorem ipsum dolor sit amet, consectetur adipiscing elit, sed do eiusmod tempor incididunt ut labore et dolore magna aliqua.</p>
  <a class="btn btn-light" style="position:absolute;left:702px;top:281px;width:167px">Shop Now</a>
  <div class="testimonial">
    <div class="avatar" role="img" aria-label="Customer portrait"></div>
    <p class="quote">"Absolutely love my lavender candle! It's my go-to after a long day. The scent is calming, and it burns beautifully!"</p>
    <b>Marla T.</b>
  </div>
</section>

<!-- Blogs -->
<h2 class="abs section-title blogs-title">Latest Blogs</h2>
<article class="abs blog" style="left:140px;top:2592px">
  <div class="shot" role="img" aria-label="Candle in amber glass beside white flowers on a wooden board" style="background:radial-gradient(ellipse 70px 60px at 55% 62%,#e8a457 0%,#9a6436 45%,rgba(60,40,28,0) 100%),linear-gradient(135deg,#c9c2b4 0%,#8a6a4c 40%,#3c2a1e 100%)"></div>
  <h3>Transform Your Bathing Ritual</h3><time>2025-01-14</time>
  <p>Lorem ipsum dolor sit amet, consectetur adipiscing elit, sed do eiusmod tempor incididunt ut labore et dolore magna aliqua.</p>
</article>
<article class="abs blog" style="left:459px;top:2592px">
  <div class="shot" role="img" aria-label="Person relaxing beside a lit candle at home" style="background:radial-gradient(ellipse 90px 70px at 55% 55%,#2f5a48 0%,#4b6b5c 40%,rgba(200,196,190,0) 100%),linear-gradient(135deg,#ecebe7,#b9b5ae 70%,#8f8b84)"></div>
  <h3>Relax and Revitalize</h3><time>2025-01-14</time>
  <p>Lorem ipsum dolor sit amet, consectetur adipiscing elit, sed do eiusmod tempor incididunt ut labore et dolore magna aliqua.</p>
</article>
<article class="abs blog" style="left:776px;top:2592px">
  <div class="shot" role="img" aria-label="Candle maker pouring wax into jars" style="background:radial-gradient(ellipse 80px 90px at 50% 40%,#4a4a4a 0%,#6e6c6a 45%,rgba(230,228,224,0) 100%),linear-gradient(180deg,#f2f1ee,#dedbd6 60%,#8a6a50)"></div>
  <h3>Fragrance In Aromatherapy</h3><time>2025-01-14</time>
  <p>Lorem ipsum dolor sit amet, consectetur adipiscing elit, sed do eiusmod tempor incididunt ut labore et dolore magna aliqua.</p>
</article>

<!-- About -->
<section class="abs about">
  <div class="about-photo" role="img" aria-label="Lit candles among spa stones and cork-stoppered oil bottles"></div>
  <div class="about-panel"></div>
  <h2>About Us</h2>
  <p style="top:134px">Lorem ipsum dolor sit amet, consectetur adipiscing elit, sed do eiusmod tempor incididunt ut labore et dolore magna aliqua. Quis ipsum suspendisse ultrices gravida. Risus commodo viverra maecenas accumsan lacus vel facilisis.</p>
  <p style="top:230px">Lorem ipsum dolor sit amet, consectetur adipiscing elit, sed do eiusmod tempor incididunt ut labore et dolore magna aliqua. Quis ipsum suspendisse ultrices gravida. Risus commodo viverra maecenas accumsan lacus vel facilisis.</p>
  <a class="btn btn-light" style="position:absolute;left:140px;top:320px;width:167px">Learn More</a>
</section>

<!-- Footer -->
<div class="abs footer-badge">VELQUINT</div>
<div class="abs fcol" style="left:350px"><h4>Information</h4><ul><li>Home</li><li>About Us</li><li>Store Location</li><li>Product Categories</li><li>FAQ</li></ul></div>
<div class="abs fcol" style="left:575px"><h4>Our Services</h4><ul><li>Delivery</li><li>Return Policy</li><li>Purchase History</li><li>Customer Service</li></ul></div>
<div class="abs fcol" style="left:831px"><h4>Contact Us</h4><ul><li>Store : #48, Fenwick Row</li><li>Street Name.</li><li>City.</li><li>Ph: 1800 555 014 2210</li><li>Mail : info@velquint.com</li></ul></div>
<div class="abs socials"><span>Vibo</span><span>Pixa</span><span>Zest</span><span>Nodo</span></div>
<div class="abs pay"><span>Karta</span><span>Duocard</span><span>Orchpay</span><span>Gleampay</span><span>vonk</span><span>Paylo</span></div>
<div class="abs copyright">© 2025 | www.velquint.com</div>

</body>
</html>
```